TalkHarbor - Language Coaching Services

Sleek, innovative, trendy design for Language Coaching business.

TalkHarbor is a new UK based company that provides Language Coaching services. We offer highly personalized on-line and face to face language courses. We also impart learning techniques workshops based on the latest neuroscience research for second-language acquisition.

Target Market(s)

See attached info

Industry/Entity Type

Consulting

Contact Information for Business Card

TalkHarbor
DaniaKV@talkharbor.co.uk
TalkHarbor.co.uk
London, UK

Font styles to use
Sans Serif

```html
<!DOCTYPE html>
<html lang="en">
<head>
<meta charset="utf-8">
<title>TalkHarbor Business Card</title>
<link href="https://fonts.googleapis.com/css2?family=Work+Sans:wght@400;500;600&family=Roboto+Condensed:wght@400&family=Roboto:wght@500&display=swap" rel="stylesheet">
<style>
  :root {
    --stage: #2b2b2b;
    --card-light: #ffffff;
    --card-dark: #2e3031;
    --brand-blue: #0a8fcf;
    --deep-blue: #0d5a8c;
    --bright-blue: #1aa6e6;
    --ink: #4a4a4a;
    --paper-text: #f2f2f2;
  }
  * { margin: 0; padding: 0; box-sizing: border-box; }
  html, body { width: 1200px; height: 930px; overflow: hidden; background: var(--stage); }
  .stage { position: relative; width: 1200px; height: 930px; }

  .card { position: absolute; left: 318px; width: 564px; height: 323px; overflow: hidden; }
  .card--front { top: 125px; background: var(--card-light); border-radius: 162px 24px 24px 162px; }
  .card--back { top: 514px; background: var(--card-dark); border-radius: 24px 162px 162px 24px; }

  .brand-mark { position: absolute; width: 256px; height: 256px; }
  .card--front .brand-mark { left: 32px; top: 33px; }
  .card--back .brand-mark { left: 276px; top: 32px; }

  .wordmark {
    position: absolute; font-family: "Work Sans", sans-serif; font-weight: 500;
    font-size: 29px; letter-spacing: 1px; color: var(--brand-blue); line-height: 1;
    white-space: nowrap;
  }
  .card--front .wordmark { right: 24px; top: 26px; }
  .card--back .wordmark { left: 22px; top: 24px; font-size: 36px; letter-spacing: 1.2px; }

  .front-info { position: absolute; right: 24px; top: 0; text-align: right; font-family: "Work Sans", sans-serif; color: var(--ink); }
  .person-name { position: absolute; right: 0; top: 97px; white-space: nowrap; font-family: "Roboto", sans-serif; font-weight: 500; font-size: 21px; letter-spacing: 1.2px; color: var(--deep-blue); }
  .person-name .surname { color: var(--bright-blue); }
  .person-role { position: absolute; right: 0; top: 124px; font-size: 14px; letter-spacing: 0.6px; }
  .address { position: absolute; right: 0; top: 172px; font-size: 14px; line-height: 20px; letter-spacing: 0.6px; white-space: nowrap; }
  .contacts { position: absolute; right: 0; top: 238px; list-style: none; font-size: 14px; line-height: 20px; letter-spacing: 0.6px; white-space: nowrap; }
  .contacts li { display: flex; justify-content: flex-end; align-items: center; gap: 7px; }
  .contacts svg { width: 9px; height: 9px; }
  .contacts .domain { color: var(--deep-blue); font-weight: 500; }

  .accent-bar { position: absolute; right: 0; top: 126px; width: 11px; height: 35px; background: linear-gradient(var(--bright-blue), var(--deep-blue)); }

  .services { position: absolute; left: 22px; top: 92px; width: 250px; font-family: "Roboto Condensed", sans-serif; color: var(--paper-text); }
  .services h2 { font-family: "Roboto", sans-serif; font-weight: 500; font-size: 20px; line-height: 24px; }
  .services .intro { margin-top: 5px; font-size: 16px; line-height: 20px; color: var(--bright-blue); white-space: nowrap; }
  .services ul { list-style: none; margin-top: 6px; font-size: 14.5px; line-height: 22.4px; white-space: nowrap; }
</style>
</head>
<body>
<main class="stage">

  <section class="card card--front" aria-label="Business card front">
    <svg class="brand-mark" viewBox="0 0 256 256" role="img" aria-label="TalkHarbor brand mark">
      <circle cx="128" cy="128" r="120" fill="none" stroke="var(--brand-blue)" stroke-width="13"/>
      <text x="128" y="136" text-anchor="middle" font-family="Work Sans, sans-serif" font-weight="500" font-size="28" fill="var(--brand-blue)">TalkHarbor</text>
    </svg>

    <div class="wordmark">TALKHARBOR</div>

    <div class="front-info">
      <p class="person-name">ARLEN <span class="surname">BROOKE</span></p>
      <p class="person-role">Director</p>
      <p class="address">52 Larkfield Road,<br>Brightmoor, UK, 4410</p>
      <ul class="contacts">
        <li>(555) 014-2297
          <svg viewBox="0 0 10 10"><path d="M2 1 L4 1 L4.6 3 L3.5 4 Q4.5 6 6 6.5 L7 5.4 L9 6 L9 8 Q5 9 2.5 6.5 Q1 4.5 2 1Z" fill="var(--deep-blue)"/></svg></li>
        <li>hello@talkharbor.co.uk
          <svg viewBox="0 0 10 10"><rect x="1" y="2.2" width="8" height="5.6" fill="none" stroke="var(--deep-blue)" stroke-width="1.2"/><path d="M1 2.5 L5 5.5 L9 2.5" fill="none" stroke="var(--deep-blue)" stroke-width="1"/></svg></li>
        <li><span>www.<span class="domain">talkharbor</span>.co.uk</span>
          <svg viewBox="0 0 10 10"><circle cx="5" cy="5" r="4" fill="none" stroke="var(--deep-blue)" stroke-width="1"/><path d="M1 5 H9 M5 1 V9" stroke="var(--deep-blue)" stroke-width="0.8"/></svg></li>
      </ul>
    </div>

    <div class="accent-bar"></div>
  </section>

  <section class="card card--back" aria-label="Business card back">
    <div class="wordmark">TALKHARBOR</div>

    <div class="services">
      <h2>Our Services</h2>
      <p class="intro">We offer highly customized coaching<br>sessions and self-study content.</p>
      <ul>
        <li>Face to face language coaching sessions</li>
        <li>On-line language coaching sessions</li>
        <li>Personalized Newsletters for self-learners</li>
        <li>Language Learning Techniques Workshops</li>
        <li>Mindful Learning Workshops</li>
        <li>Access to premium content, resources.</li>
      </ul>
    </div>

    <svg class="brand-mark" viewBox="0 0 256 256" role="img" aria-label="TalkHarbor brand mark">
      <circle cx="128" cy="128" r="120" fill="none" stroke="var(--brand-blue)" stroke-width="13"/>
      <text x="128" y="136" text-anchor="middle" font-family="Work Sans, sans-serif" font-weight="500" font-size="28" fill="var(--brand-blue)">TalkHarbor</text>
    </svg>
  </section>

</main>
</body>
</html>
```